Banner Pop Up Opt In Form REDESIGNS - SLEEK BLACK LOOK

Please redesign banners attached.

I am looking for a very sleek look....I do not like this collage of images on these current designs. Please keep all content same but use images that pop.

I have an acccount at www.pixvane-example.com or you can use your own images.

I like black background for somereason because it looks very sleek....but these designs should pop , build trust and credibility and have easy opt in form....SLEEK AND MODERN LOOK is what im looking for....

Target Market(s)

Consumers on websites

Requirements
Must have
• Please redesign banners attached.

Nice to have

Should not have

```html
<!DOCTYPE html>
<html lang="en">
<head>
<meta charset="utf-8">
<title>Smart Fitness Watch – Newsletter Opt In</title>
<link rel="stylesheet" href="https://fonts.googleapis.com/css2?family=Montserrat:wght@500;800&family=Poppins:wght@300;400&display=swap">
<style>
  :root {
    --ink: #000000;
    --accent: #f79f1c;
    --paper: #ffffff;
    --photo-light: #5a5a5a;
    --photo-dark: #2b2b2b;
    --device-light: #4a4a4a;
    --device-dark: #151515;
  }
  html, body {
    margin: 0;
    padding: 0;
    width: 1200px;
    height: 1200px;
    overflow: hidden;
    background: var(--paper);
  }
  .banner {
    display: block;
    width: 1200px;
    height: 1200px;
  }
  .headline {
    font-family: "Montserrat", sans-serif;
    font-weight: 800;
    fill: var(--accent);
  }
  .subline {
    font-family: "Montserrat", sans-serif;
    font-weight: 500;
    fill: var(--paper);
  }
  .product-name {
    font-family: "Montserrat", sans-serif;
    font-weight: 800;
    fill: var(--paper);
  }
  .product-name--accent { fill: var(--accent); }
  .field-label {
    font-family: "Poppins", sans-serif;
    font-weight: 300;
    fill: var(--paper);
  }
  .field-line { fill: var(--paper); }
  .submit-button { fill: var(--accent); }
  .submit-label {
    font-family: "Poppins", sans-serif;
    font-weight: 400;
    fill: var(--paper);
  }
  .redeem-note {
    font-family: "Poppins", sans-serif;
    font-weight: 300;
    fill: var(--paper);
  }
</style>
</head>
<body>
<svg class="banner" viewBox="0 0 1670 1670" xmlns="http://www.w3.org/2000/svg">
  <defs>
    <linearGradient id="workout-tones" x1="0" y1="0" x2="1" y2="1">
      <stop offset="0" stop-color="var(--photo-light)"/>
      <stop offset="0.55" stop-color="#474444"/>
      <stop offset="1" stop-color="var(--photo-dark)"/>
    </linearGradient>
    <radialGradient id="device-tones" cx="0.5" cy="0.45" r="0.6">
      <stop offset="0" stop-color="var(--device-light)"/>
      <stop offset="1" stop-color="var(--device-dark)"/>
    </radialGradient>
  </defs>

  <!-- Background scene -->
  <rect class="workout-scene" role="img" aria-label="Group fitness class doing side planks in a gym" x="0" y="0" width="1670" height="1670" fill="url(#workout-tones)"/>

  <!-- Header panel with accent band -->
  <path class="accent-band" fill="var(--accent)" d="M0 0 H1455 L1595 290 Q1640 400 1590 480 Q1555 535 1480 560 L0 1035 Z"/>
  <path class="header-panel" fill="var(--ink)" d="M0 0 H1410 L1555 300 Q1600 400 1555 460 Q1525 500 1460 520 L0 995 Z"/>

  <!-- Offer copy -->
  <text class="headline" x="85" y="158" font-size="104" textLength="1190" lengthAdjust="spacingAndGlyphs">WANT A GREAT OFFER?</text>
  <text class="subline" x="85" y="226" font-size="40" textLength="1280" lengthAdjust="spacingAndGlyphs">SUBSCRIBE TO OUR NEWSLETTER AND RECIEVE COMPLEMENTARY</text>

  <!-- Product -->
  <rect class="product-shot" role="img" aria-label="Black smart fitness watch showing a step count" x="92" y="340" width="325" height="390" rx="40" fill="url(#device-tones)"/>
  <text class="product-name" x="550" y="428" font-size="82" textLength="648" lengthAdjust="spacingAndGlyphs">SMART FITNESS</text>
  <text class="product-name product-name--accent" x="550" y="558" font-size="128" textLength="465" lengthAdjust="spacingAndGlyphs">WATCH</text>

  <!-- Opt in form -->
  <g class="optin-form">
    <text class="field-label" x="85" y="1155" font-size="52">Name</text>
    <rect class="field-line" x="77" y="1180" width="773" height="4"/>
    <text class="field-label" x="85" y="1282" font-size="52">Email</text>
    <rect class="field-line" x="77" y="1314" width="773" height="4"/>
    <text class="field-label" x="85" y="1422" font-size="52">Phone</text>
    <rect class="field-line" x="77" y="1448" width="773" height="4"/>

    <rect class="submit-button" x="85" y="1525" width="248" height="67" rx="22"/>
    <text class="submit-label" x="209" y="1576" font-size="48" text-anchor="middle">Submit</text>
  </g>

  <text class="redeem-note" font-size="30">
    <tspan x="818" y="1570">we will send an email and a text message with the</tspan>
    <tspan x="818" y="1605">offer and instructions on how to redeem</tspan>
  </text>
</svg>
</body>
</html>
```